Harlow Advisory, Business Cards for International Development Consultancy

I'm an independent consultant working in the international development sector. I work with small organisations in developing countries to help them develop their community based programs so that they can be internationally competitive. This means they need to work better with their own communities to deliver meaningful quality work and also improve the accountability of their work so that they can compete for international and domestic funding.

I like the idea of being a connector between community, local organisations and international best practice and back again (ie acknowledging that international best practice can learn a lot from community).

My surname is Harlow - so I'd like the logo to use the idea of web as a connector.

I work with people with sight impairments - would like my card to be useful for low vision (i.e. clear graphics, easy to read font) and no vision (i.e. brail).

Target Market(s)

international non-government organisations (i.e. pelmark, lift the hamlets, kindred arc), Blue Shield Gold Lantern, government (i.e. Australian Bureau of Overseas Relations, consulars), non government agencies,

Industry/Entity Type

Business

Contact Information for Business Card

International Development Consultant
Connecting International Development with Community

Marcia Harlow
Lead Consultant
Phone: +61 412 583720
Email: mharlow.advisory@postnest.example

Font styles to use
Sans Serif

Colors
eaf1f7
85acd3
d3a5cc
0456a4
a64599
0255a3

Requirements
Nice to have
• brail
Should not have
• fancy fonts - needs to be easy to read.

```html
<!DOCTYPE html>
<html lang="en">
<head>
<meta charset="utf-8">
<title>Harlow Advisory – Business Cards</title>
<link rel="stylesheet" href="https://fonts.googleapis.com/css2?family=Exo+2:wght@700;800&family=Montserrat:wght@400;500;600&display=swap">
<style>
  :root {
    --backdrop: #e9e7e4;
    --blue-light: #1fa6bd;
    --blue-mid: #1690b8;
    --blue-deep: #0f6fa6;
    --white: #ffffff;
    --white-soft: rgba(255, 255, 255, 0.82);
    --paper: #fbfbfb;
    --stripe: #ececec;
    --teal: #3ec2ad;
    --grey: #8a8a8a;
    --ink: #3a3a3a;
  }
  * { box-sizing: border-box; margin: 0; padding: 0; }
  html, body { width: 1200px; height: 800px; overflow: hidden; }
  body {
    background: var(--backdrop);
    font-family: "Montserrat", Arial, sans-serif;
    display: flex;
    align-items: center;
    justify-content: center;
    gap: 48px;
  }
  .card {
    position: relative;
    width: 525px;
    height: 300px;
    border-radius: 4px;
    overflow: hidden;
    box-shadow: 0 10px 28px rgba(0, 0, 0, 0.18);
  }

  /* Front */
  .card-front {
    background: linear-gradient(160deg, var(--blue-light) 0%, var(--blue-mid) 55%, var(--blue-deep) 100%);
    color: var(--white);
  }
  .card-front .pattern-area {
    position: absolute; inset: 0;
    background: radial-gradient(circle at 50% 40%, rgba(255,255,255,0.10), rgba(255,255,255,0) 70%);
  }
  .brand {
    position: absolute;
    left: 60px; top: 58px;
  }
  .brand-name {
    font-family: "Exo 2", Arial, sans-serif;
    font-weight: 800;
    font-size: 78px;
    line-height: 0.9;
    letter-spacing: 7px;
  }
  .brand-sub {
    font-family: "Exo 2", Arial, sans-serif;
    font-weight: 700;
    font-size: 38px;
    letter-spacing: 3px;
    line-height: 1.1;
  }
  .brand-role {
    font-size: 12px;
    font-weight: 600;
    letter-spacing: 1.2px;
    margin-top: 4px;
  }
  .tagline {
    position: absolute;
    left: 20px; right: 20px; bottom: 18px;
    font-size: 12px;
    font-weight: 500;
    letter-spacing: 1.4px;
    color: var(--white-soft);
    text-align: center;
  }

  /* Back */
  .card-back { background: var(--paper); color: var(--ink); }
  .card-back .pattern-area {
    position: absolute; inset: 0;
    background: linear-gradient(135deg, var(--paper) 0%, var(--stripe) 50%, var(--paper) 100%);
  }
  .person {
    position: absolute;
    left: 150px; top: 34px;
  }
  .person-name {
    font-size: 26px;
    font-weight: 600;
    letter-spacing: 3px;
    color: var(--teal);
    text-transform: uppercase;
  }
  .person-title {
    font-size: 13px;
    letter-spacing: 1.5px;
    color: var(--grey);
    text-transform: uppercase;
    margin-top: -2px;
  }
  .contact {
    position: absolute;
    right: 28px; bottom: 34px;
    list-style: none;
  }
  .contact li {
    display: flex;
    align-items: center;
    justify-content: flex-end;
    gap: 12px;
    font-size: 16px;
    line-height: 28px;
    color: var(--ink);
  }
  .contact svg { width: 22px; height: 22px; flex: none; }
</style>
</head>
<body>

<section class="card card-front" aria-label="Business card front">
  <div class="pattern-area" role="img" aria-label="Faint concentric web-line pattern"></div>
  <div class="brand">
    <div class="brand-name">HARLOW</div>
    <div class="brand-sub">ADVISORY</div>
    <div class="brand-role">INTERNATIONAL DEVELOPMENT CONSULTANT</div>
  </div>
  <p class="tagline">CONNECTING INTERNATIONAL DEVELOPMENT WITH COMMUNITY</p>
</section>

<section class="card card-back" aria-label="Business card back">
  <div class="pattern-area" role="img" aria-label="Light grey angled stripe pattern"></div>
  <div class="person">
    <h1 class="person-name">Marcia Harlow</h1>
    <p class="person-title">Lead Consultant</p>
  </div>
  <ul class="contact">
    <li>+61 412 583720
      <svg viewBox="0 0 22 22" aria-hidden="true">
        <circle cx="11" cy="11" r="11" fill="#3ec2ad"/>
        <rect x="7.5" y="5" width="7" height="12" rx="1.2" fill="none" stroke="#fff" stroke-width="1.4"/>
        <line x1="10" y1="15" x2="12" y2="15" stroke="#fff" stroke-width="1.2"/>
      </svg>
    </li>
    <li>mharlow.advisory@postnest.example
      <svg viewBox="0 0 22 22" aria-hidden="true">
        <circle cx="11" cy="11" r="11" fill="#3ec2ad"/>
        <rect x="5.5" y="7" width="11" height="8" fill="none" stroke="#fff" stroke-width="1.3"/>
        <polyline points="5.5,7 11,11.5 16.5,7" fill="none" stroke="#fff" stroke-width="1.3"/>
      </svg>
    </li>
  </ul>
</section>

</body>
</html>
```